Institutional website for an IT Consulting company

Web design + HTML + CSS / Bootstrap + JS (interaction) integration in order to extend our existing website brightvale.coop.
Our website is currently aiming only for recruitment and not for customers, we want to provide a fluid transition between customer side website (this project) and recruitment website (existing site).

Ideally we would love the new design to be "inspired" by our actual graphic chart (Colors mainly). It should provide a great user experience and a landing page (or any mean) allowing the visitor to easily switch from the end customer front end (this project), the recruitment front end (existing front end https://www.brightvale.coop/) and the existing member front end (an other existing front end dedicated to members already existing).

In attachment you will find the expected site content mainly a one page with a first level of information and "link" to sub pages (a way to directly access this sub pages should also be provided).

The website should be accessible on mobile device and desktop.

The attachment is in french as it reflect the final site content, but if google translate isn't sufficient to have a general idea of the content, feel free to ask. We would love to have some visual representation for some categories.

Target Market(s)

fortune 500 companies

Industry/Entity Type

It Company

Coding

Coded - Design and coding required

Number of Pages Required

5+ page

Requirements
Must have
• This project must have an easy way to navigate between 3 sub sites, the customer one (the one designed here), the consultant / recruitment one (the existing one at brightvale.coop), the members one.

A one page experience at first leading to detail pages.

Custom made visuals to illustrate each categories.

Inspiration websites : pirog[.]fr ; tasklynn[.]com ; dorvelo[.] com ...

Be inspired by the existing color from our logo and existing website at brightvale[.]coop

```html
<!DOCTYPE html>
<html lang="en">
<head>
<meta charset="utf-8">
<title>Brightvale.coop — Digital services for enterprises</title>
<link href="https://fonts.googleapis.com/css2?family=Poppins:wght@600;700&family=Rubik:wght@400;500;600;700&display=swap" rel="stylesheet">
<style>
  :root {
    --teal: #1aa1a9;
    --ink: #0f3a36;
    --text: #2d2d2d;
    --blush: #f5f1f1;
    --night: #2b2a2c;
    --white: #ffffff;
  }
  * { box-sizing: border-box; margin: 0; padding: 0; }
  html, body { width: 1200px; height: 2996px; overflow: hidden; background: var(--white); }
  body { font-family: "Rubik", sans-serif; color: var(--text); }
  .page { position: relative; width: 1200px; height: 2996px; overflow: hidden; }
  .abs { position: absolute; }

  .hero-wash { position: absolute; left: 0; top: 0; }

  .brand { position: absolute; font-family: "Poppins", sans-serif; font-weight: 700; color: var(--ink); line-height: 1; }
  .brand .name { font-size: 46px; letter-spacing: 0.5px; display: block; }
  .brand .tld { font-size: 22px; display: block; text-align: right; margin-top: 2px; }
  .brand--light { color: var(--white); }

  .nav { position: absolute; font-family: "Poppins", sans-serif; font-weight: 600; font-size: 17px; color: var(--ink); }
  .nav a { color: inherit; text-decoration: none; position: absolute; white-space: nowrap; }
  .nav--light { color: var(--white); }

  .hero-title { left: 131px; top: 244px; width: 400px; font-family: "Poppins", sans-serif; font-weight: 700; font-size: 31px; line-height: 38.5px; color: var(--ink); letter-spacing: -0.3px; }
  .btn { position: absolute; background: var(--teal); color: var(--white); font-family: "Poppins", sans-serif; font-weight: 700; font-size: 17px; display: flex; align-items: center; justify-content: center; text-decoration: none; }

  .frame { position: absolute; background: var(--teal); }
  .photo { position: absolute; }

  .card { position: absolute; width: 198px; height: 163px; border: 3px solid var(--teal); background: var(--white); display: flex; flex-direction: column; align-items: center; }
  .card svg { margin-top: 27px; }
  .card span { position: absolute; top: 94px; left: 0; right: 0; text-align: center; font-weight: 600; font-size: 13px; line-height: 19px; color: var(--teal); letter-spacing: 0.4px; text-transform: uppercase; }
  .card span.single { top: 103px; }

  .section-title { position: absolute; font-weight: 600; font-size: 26px; letter-spacing: 0.5px; }
  .rule { position: absolute; height: 1px; width: 40px; background: #9a9a9a; }

  .reasons { position: absolute; left: 664px; top: 1296px; width: 410px; list-style: none; font-size: 15px; line-height: 21px; color: #333; }
  .reasons li { position: absolute; left: 27px; width: 390px; }
  .reasons li::before { content: ""; position: absolute; left: -30px; top: 8px; width: 7px; height: 7px; border-right: 2px solid #777; border-top: 2px solid #777; transform: rotate(45deg); }

  .band { position: absolute; left: 0; top: 1736px; }
  .sim-title { left: 155px; top: 1815px; color: var(--white); font-size: 26px; }
  .field-label { position: absolute; top: 1910px; font-size: 10.5px; font-weight: 700; color: var(--white); letter-spacing: 0.3px; }
  .field { position: absolute; top: 1930px; width: 177px; height: 41px; border: 3px solid var(--white); color: var(--white); font-size: 12.5px; font-weight: 500; display: flex; align-items: center; padding-left: 11px; }
  .result { position: absolute; top: 2014px; width: 204px; height: 120px; background: var(--white); text-align: center; }
  .result strong { display: block; margin-top: 33px; font-size: 20px; font-weight: 500; color: var(--teal); }
  .result small { display: block; margin-top: 10px; font-size: 12px; line-height: 15px; color: #333; text-transform: uppercase; }

  .team-title { left: 131px; top: 2348px; font-weight: 700; font-size: 37px; line-height: 46px; color: #111; letter-spacing: 0.5px; }

  .footer { position: absolute; left: 0; top: 2735px; width: 1200px; height: 261px; background: var(--night); }
  .follow { position: absolute; left: 879px; top: 2793px; color: var(--white); font-family: "Poppins", sans-serif; font-weight: 600; font-size: 17px; }
  .dot { position: absolute; top: 2790px; width: 26px; height: 26px; border-radius: 50%; }
  .footer-rule { position: absolute; left: 131px; top: 2902px; width: 937px; height: 1px; background: #4a494b; }
  .copyright { position: absolute; left: 0; width: 1200px; top: 2944px; text-align: center; color: #d8d8d8; font-size: 12px; }
</style>
</head>
<body>
<div class="page">

  <svg class="hero-wash" width="1200" height="1140" viewBox="0 0 1200 1140" aria-hidden="true">
    <polygon points="0,0 1200,0 1200,99 0,1137" fill="var(--blush)"/>
  </svg>

  <header>
    <div class="brand" style="left:131px; top:30px;">
      <span class="name">BRIGHTVALE</span>
      <span class="tld">.COOP</span>
    </div>
    <nav class="nav" style="left:0; top:50px;">
      <a href="#" style="left:540px;">Find an expert</a>
      <a href="#" style="left:721px;">Members area</a>
      <a href="#" style="left:887px;">Join Brightvale</a>
    </nav>
  </header>

  <section class="hero">
    <h1 class="abs hero-title">BRIGHTVALE.COOP<br>delivers expert<br>digital services to<br>large enterprises,<br>cooperatively.</h1>
    <a class="btn" href="#" style="left:135px; top:474px; width:136px; height:41px;">READ MORE</a>
    <div class="frame" style="left:542px; top:138px; width:528px; height:508px;"></div>
    <div class="photo" role="img" aria-label="Consultant presenting to a client team in a bright glass-walled meeting room"
         style="left:572px; top:172px; width:460px; height:441px; background:linear-gradient(160deg,#e9ecee 0%,#c9cdd1 45%,#6e6a66 100%);"></div>
  </section>

  <section class="profiles" aria-label="Services">
    <div class="card" style="left:171px; top:769px;">
      <svg width="40" height="46" viewBox="0 0 40 46"><circle cx="20" cy="11" r="9" fill="var(--teal)"/><path d="M2 46 Q2 24 20 24 Q38 24 38 46 Z" fill="var(--teal)"/></svg>
      <span>Technical<br>assistance</span>
    </div>
    <div class="card" style="left:388px; top:769px;">
      <svg width="44" height="42" viewBox="0 0 44 42"><rect x="15" y="2" width="14" height="8" rx="2" fill="none" stroke="var(--teal)" stroke-width="3"/><rect x="1" y="9" width="42" height="31" rx="3" fill="var(--teal)"/><rect x="19" y="20" width="6" height="6" fill="#fff"/></svg>
      <span>Project<br>delivery</span>
    </div>
    <div class="card" style="left:607px; top:769px;">
      <svg width="40" height="40" viewBox="0 0 40 40"><rect x="3" y="7" width="28" height="29" rx="3" fill="none" stroke="var(--teal)" stroke-width="3.5"/><path d="M14 25 L33 5 L37 9 L18 28 L13 29 Z" fill="var(--teal)"/></svg>
      <span class="single">Audit</span>
    </div>
    <div class="card" style="left:824px; top:769px;">
      <svg width="64" height="40" viewBox="0 0 64 40"><path d="M2 6 L14 4 L20 26 L8 30 Z" fill="var(--teal)"/><path d="M62 6 L50 4 L44 26 L56 30 Z" fill="var(--teal)"/><path d="M18 10 L30 8 L38 12 L46 10 L46 26 L34 36 L22 28 Z" fill="none" stroke="var(--teal)" stroke-width="3"/></svg>
      <span class="single">Partnership</span>
    </div>
    <div class="card" style="left:171px; top:955px;">
      <svg width="46" height="48" viewBox="0 0 46 48"><circle cx="20" cy="20" r="17" fill="none" stroke="var(--teal)" stroke-width="3.5"/><circle cx="20" cy="16" r="5" fill="var(--teal)"/><path d="M11 30 Q20 20 29 30 Z" fill="var(--teal)"/><path d="M32 32 L44 45" stroke="var(--teal)" stroke-width="5" stroke-linecap="round"/></svg>
      <span class="single">Sourcing</span>
    </div>
    <div class="card" style="left:388px; top:955px;">
      <svg width="60" height="44" viewBox="0 0 60 44"><circle cx="30" cy="7" r="6" fill="var(--teal)"/><path d="M20 44 V24 Q20 15 30 15 Q40 15 40 24 V44 Z" fill="var(--teal)"/><circle cx="15" cy="14" r="5" fill="var(--teal)"/><path d="M7 44 V28 Q7 21 15 21 Q18 21 19 23 V44 Z" fill="var(--teal)"/><circle cx="45" cy="14" r="5" fill="var(--teal)"/><path d="M53 44 V28 Q53 21 45 21 Q42 21 41 23 V44 Z" fill="var(--teal)"/><circle cx="4" cy="22" r="3.5" fill="var(--teal)"/><circle cx="56" cy="22" r="3.5" fill="var(--teal)"/></svg>
      <span class="single">Teams</span>
    </div>
    <div class="card" style="left:607px; top:955px;">
      <svg width="50" height="44" viewBox="0 0 50 44"><rect x="16" y="2" width="32" height="22" rx="3" fill="none" stroke="var(--teal)" stroke-width="3"/><rect x="9" y="8" width="32" height="22" rx="3" fill="#fff" stroke="var(--teal)" stroke-width="3"/><path d="M5 14 H33 Q36 14 36 17 V33 Q36 36 33 36 H14 L6 42 V36 Q2 36 2 33 V17 Q2 14 5 14 Z" fill="#fff" stroke="var(--teal)" stroke-width="3"/><path d="M9 23 H29 M9 29 H24" stroke="var(--teal)" stroke-width="2.5"/></svg>
      <span class="single">Consulting</span>
    </div>
    <div class="card" style="left:824px; top:955px;">
      <svg width="40" height="58" viewBox="0 0 40 58" style="margin-top:24px"><circle cx="20" cy="13" r="10" fill="var(--teal)"/><rect x="12" y="10" width="16" height="5" rx="2" fill="#fff"/><path d="M4 58 V34 Q4 26 20 26 Q36 26 36 34 V58 Z" fill="var(--teal)"/><rect x="0" y="40" width="40" height="18" fill="#fff"/><rect x="4" y="42" width="32" height="16" rx="2" fill="var(--teal)"/><circle cx="20" cy="50" r="2" fill="#fff"/></svg>
      <span class="single">Development</span>
    </div>
  </section>

  <section class="why">
    <h2 class="section-title" style="left:0; width:1200px; text-align:center; top:1189px; color:#111;">WHY WORK WITH US?</h2>
    <div class="rule" style="left:564px; top:1240px;"></div>
    <div class="photo" role="img" aria-label="Smiling consultant in shirt and tie holding an open laptop"
         style="left:93px; top:1262px; width:570px; height:500px; z-index:2; background:linear-gradient(180deg,#fbfbfc 0%,#eef2f6 55%,#d7e3ee 100%);"></div>
    <ul class="reasons">
      <li style="top:10px;">Senior experts selected for their skills<br>and committed to your results.</li>
      <li style="top:76px;">A single point of contact who follows your project from the first brief to final delivery.</li>
      <li style="top:146px;">Consultants who are partners of the cooperative, with a real stake in the quality and success of each mission.</li>
      <li style="top:237px;">Knowledge shared within a group of recognized experts across every digital field.</li>
      <li style="top:303px;">Transparent rates with no hidden margins, a fair alternative to the model of traditional IT services companies.</li>
      <li style="top:389px;">Teams that scale with your needs, from a single expert to a full squad.</li>
    </ul>
  </section>

  <section class="simulator">
    <svg class="band" width="1200" height="466" viewBox="0 0 1200 466" aria-hidden="true">
      <polygon points="0,0 1200,56 1200,466 0,466" fill="var(--teal)"/>
    </svg>
    <h2 class="section-title sim-title">ESTIMATE YOUR PROJECT</h2>
    <div class="rule" style="left:157px; top:1861px; background:#fff;"></div>

    <label class="field-label" style="left:157px;">DAILY RATE (HT)</label>
    <label class="field-label" style="left:356px;">DAYS NEEDED</label>
    <label class="field-label" style="left:555px;">EXPERTS</label>
    <div class="field" style="left:157px;">€ 600</div>
    <div class="field" style="left:356px;">217</div>
    <div class="field" style="left:555px;">1</div>

    <div class="result" style="left:156px;"><strong>€ 10,850</strong><small>Monthly<br>budget (HT)</small></div>
    <div class="result" style="left:374px;"><strong>€ 130,200</strong><small>Annual<br>budget (HT)</small></div>
    <div class="result" style="left:593px;"><strong>48 h</strong><small>First profiles<br>proposed</small></div>
    <div class="result" style="left:813px;"><strong>10 days</strong><small>Average<br>start time</small></div>
  </section>

  <section class="team">
    <h2 class="abs team-title">A DEDICATED TEAM<br>SUPPORTS YOUR<br>BUSINESS</h2>
    <a class="btn" href="#" style="left:135px; top:2519px; width:149px; height:41px;">CONTACT US</a>
    <div class="frame" style="left:573px; top:2255px; width:496px; height:424px;"></div>
    <div class="photo" role="img" aria-label="Account manager working on a laptop at a desk in front of honeycomb shelves"
         style="left:601px; top:2283px; width:434px; height:369px; background:linear-gradient(150deg,#d9b877 0%,#e8dcc4 45%,#f1efeb 70%,#cfc9c2 100%);"></div>
  </section>

  <footer>
    <div class="footer"></div>
    <div class="brand brand--light" style="left:131px; top:2788px;">
      <span class="name">BRIGHTVALE</span>
      <span class="tld">.COOP</span>
    </div>
    <div class="follow">Follow us</div>
    <div class="dot" style="left:975px; background:#3b5bb0;"></div>
    <div class="dot" style="left:1009px; background:#1e9be0;"></div>
    <div class="dot" style="left:1043px; background:#1d2a8f;"></div>
    <nav class="nav nav--light" style="left:0; top:2844px;">
      <a href="#" style="left:538px;">Find an expert</a>
      <a href="#" style="left:720px;">Members area</a>
      <a href="#" style="left:886px;">Join Brightvale</a>
    </nav>
    <div class="footer-rule"></div>
    <p class="copyright">Copyright © 2020 All Rights Reserved</p>
  </footer>

</div>
</body>
</html>
```